Business Card Design

We like to use greens as you will see in our logo (but not TOO much green). We are a Dental Clinic in a somewhat eccentric community. We do not like the dated sharp designs which we see many dentists use. We're looking for something bright and fresh while still maintaining the integrity of the profession. Elegance is not necessarily what we are going for... we need for the design to be "mature" but also up-lifting.

See our logo.
Updates

Project Deadline Extended
Reason: We have 5 designs which we like. But we'd like to see a few more before committing to a design.

Project Deadline Extended
Reason: We are awaiting revisions to this project. We are still welcoming designs while we wait to see if designers are able to provide to us the revisions we require in order to proceed with a selection.

Target Market(s)

Younger families - ages late 20's to early 40's

Industry/Entity Type

Business

Contact Information for Business Card

Corwel T. Banfry DDS 2730 W. Halvert Rd. Ste. 7 Fernvale, OH 48391 (555)555-0174 FX (555)555-0189 info@BrightwellDentalCareMi.com BrigthwellDentalCareMi.com on the back of the card we need an appointment reminder (For____ Date___ Time____) with "If you are unable to keep your appointment, kindly give 48 hours notice" at the bottom. No use of teeth in the design. DOUBLE SIDED DESIGN

Requirements
Should not have
• The use of pictures of teeth

```html
<!DOCTYPE html>
<html lang="en">
<head>
<meta charset="utf-8">
<title>Brightwell Dental Care – Business Card</title>
<link rel="stylesheet" href="https://fonts.googleapis.com/css2?family=Arimo:wght@400;700&family=Source+Sans+3:ital,wght@0,400;1,400&family=Cinzel:wght@500&display=swap">
<style>
  :root {
    --backdrop: #ececec;
    --card: #ffffff;
    --green-dark: #1e6b3a;
    --green-mid: #2e9e4a;
    --green-line: #7dc242;
    --green-soft: #9fd36a;
    --ink: #3a3a3a;
    --ink-name: #4a4a4a;
    --ribbon-light: #ffffff;
    --ribbon-dark: #d6d6d6;
  }
  * { margin: 0; padding: 0; box-sizing: border-box; }
  html, body { width: 1200px; height: 1160px; overflow: hidden; background: var(--backdrop); }
  body { position: relative; font-family: "Source Sans 3", Arial, sans-serif; color: var(--ink); }

  .card {
    position: absolute;
    background: var(--card);
    border-radius: 33px;
    overflow: hidden;
    box-shadow: 0 2px 8px rgba(0,0,0,0.12);
  }
  .card-front { left: 264px; top: 27px; width: 912px; height: 517px; }
  .card-back  { left: 47px;  top: 587px; width: 910px; height: 518px; }
  .card-shapes { position: absolute; inset: 0; }
  .abs { position: absolute; white-space: nowrap; }

  /* Front */
  .doctor-name {
    left: 44px; top: 98px;
    font-family: "Arimo", Arial, sans-serif; font-weight: 700;
    font-size: 31px; color: var(--ink-name);
  }
  .doctor-name .credential { font-size: 21px; }
  .address {
    right: 44px; top: 148px; text-align: right;
    font-family: "Arimo", Arial, sans-serif; font-size: 22px; line-height: 35px; color: var(--ink);
  }
  .brand { display: flex; align-items: center; gap: 14px; }
  .brand-dot { width: 46px; height: 46px; border-radius: 50%; background: var(--green-soft); flex: none; }
  .brand-name {
    font-family: "Source Sans 3", Arial, sans-serif; font-weight: 400;
    color: var(--green-dark); line-height: 1;
  }
  .brand-front { left: 59px; top: 262px; }
  .brand-front .brand-name { font-size: 50px; }
  .brand-front .brand-name small { display: block; font-size: 34px; margin-top: 6px; }
  .contact-list {
    right: 44px; top: 298px; list-style: none; text-align: right;
    font-family: "Arimo", Arial, sans-serif; font-size: 22px; line-height: 43px; color: var(--ink);
  }
  .contact-list li { display: flex; justify-content: flex-end; align-items: center; gap: 8px; }
  .contact-list svg { width: 20px; height: 20px; fill: var(--ink); }
  .website {
    right: 44px; top: 468px;
    font-family: "Arimo", Arial, sans-serif; font-size: 22px; letter-spacing: 1.5px; color: #fff;
  }

  /* Back */
  .appt-title {
    left: 71px; top: 92px;
    font-family: "Cinzel", Georgia, serif; font-weight: 500; font-size: 34px;
    letter-spacing: 1px; color: var(--green-dark);
  }
  .brand-back { right: 55px; top: 46px; }
  .brand-back .brand-name { font-size: 44px; }
  .brand-back .brand-name small { display: block; font-size: 30px; margin-top: 4px; }
  .form-label { font-size: 25px; color: var(--ink); }
  .day-label {
    font-family: "Arimo", Arial, sans-serif; font-weight: 700; font-size: 23px; color: #fff;
    top: 383px;
  }
  .notice {
    left: 0; right: 0; top: 458px; text-align: center;
    font-style: italic; font-size: 25px; color: var(--ink);
  }
</style>
</head>
<body>

<section class="card card-front" aria-label="Business card front">
  <svg class="card-shapes" viewBox="0 0 912 517" width="912" height="517">
    <defs>
      <linearGradient id="ribbon-shade" x1="0" y1="0" x2="1" y2="0">
        <stop offset="0.35" stop-color="var(--ribbon-light)"/>
        <stop offset="1" stop-color="var(--ribbon-dark)"/>
      </linearGradient>
    </defs>
    <path class="ribbon" d="M0 59 L360 59 C470 59 520 114 640 114 L912 112 L912 248 L700 248 C560 248 500 185 380 185 L0 185 Z" fill="url(#ribbon-shade)"/>
    <path class="ribbon-edge" d="M0 59 L360 59 C470 59 520 114 640 114 L912 112" fill="none" stroke="var(--green-line)" stroke-width="3"/>
    <path class="ribbon-edge" d="M0 185 L380 185 C500 185 560 248 700 248 L912 246" fill="none" stroke="var(--green-line)" stroke-width="3"/>
    <rect class="footer-band" x="0" y="444" width="912" height="73" fill="var(--green-dark)"/>
  </svg>

  <div class="abs doctor-name">CORWEL T. BANFRY, <span class="credential">DDS</span></div>
  <div class="abs address">2730 W. Halvert Rd.<br>Ste. 7 Fernvale, OH 48391</div>

  <div class="abs brand brand-front">
    <span class="brand-dot"></span>
    <span class="brand-name">Brightwell<small>Dental Care</small></span>
  </div>

  <ul class="abs contact-list">
    <li><svg viewBox="0 0 24 24"><path d="M6.6 10.8a15 15 0 0 0 6.6 6.6l2.2-2.2c.3-.3.7-.4 1-.2 1.1.4 2.3.6 3.6.6.6 0 1 .4 1 1V20c0 .6-.4 1-1 1A17 17 0 0 1 3 4c0-.6.4-1 1-1h3.5c.6 0 1 .4 1 1 0 1.3.2 2.5.6 3.6.1.3 0 .7-.2 1z"/></svg>(555) 555-0174</li>
    <li><svg viewBox="0 0 24 24"><path d="M7 3h10v5H7zM4 9h16a2 2 0 0 1 2 2v6h-4v4H6v-4H2v-6a2 2 0 0 1 2-2zm4 7v3h8v-3z"/></svg>(555) 555-0189</li>
    <li><svg viewBox="0 0 24 24"><path d="M3 9l9-6 9 6v10H3zm2 1.2V17h14v-6.8l-7 4.6z"/></svg>info@BrightwellDentalCareMi.com</li>
  </ul>

  <div class="abs website">www.BrightwellDentalCareMi.com</div>
</section>

<section class="card card-back" aria-label="Appointment card back">
  <svg class="card-shapes" viewBox="0 0 910 518" width="910" height="518">
    <g class="dotted-lines" stroke="#555" stroke-width="2" stroke-dasharray="1.5 3">
      <line x1="182" y1="205" x2="848" y2="205"/>
      <line x1="182" y1="270" x2="412" y2="270"/>
      <line x1="498" y1="270" x2="738" y2="270"/>
    </g>
    <g class="next-boxes" fill="#fff" stroke="#555" stroke-width="2">
      <rect x="328" y="305" width="163" height="35" rx="6"/>
      <rect x="504" y="305" width="163" height="35" rx="6"/>
      <rect x="677" y="305" width="165" height="35" rx="6"/>
    </g>
    <rect class="day-band" x="0" y="359" width="722" height="77" fill="var(--green-dark)"/>
    <rect class="day-band-sat" x="722" y="359" width="188" height="77" fill="var(--green-mid)"/>
    <line x1="722" y1="359" x2="722" y2="436" stroke="#fff" stroke-width="3"/>
    <g class="day-boxes" fill="#fff" stroke="#555" stroke-width="1.5">
      <rect x="157" y="382" width="57" height="32" rx="5"/>
      <rect x="289" y="382" width="57" height="32" rx="5"/>
      <rect x="430" y="382" width="57" height="32" rx="5"/>
      <rect x="568" y="382" width="56" height="32" rx="5"/>
      <rect x="689" y="382" width="57" height="32" rx="5"/>
      <rect x="819" y="382" width="56" height="32" rx="5"/>
    </g>
  </svg>

  <div class="abs appt-title">YOUR APPOINTMENT</div>
  <div class="abs brand brand-back">
    <span class="brand-name">Brightwell<small>Dental Care</small></span>
  </div>

  <div class="abs form-label" style="left:80px; top:176px;">Name :</div>
  <div class="abs form-label" style="left:80px; top:241px;">Date :</div>
  <div class="abs form-label" style="left:417px; top:241px;">Time :</div>
  <div class="abs form-label" style="left:747px; top:241px;">am / pm</div>
  <div class="abs form-label" style="left:80px; top:305px;">Next Appointment</div>

  <div class="abs day-label" style="left:80px;">MON</div>
  <div class="abs day-label" style="left:226px;">TUE</div>
  <div class="abs day-label" style="left:357px;">WED</div>
  <div class="abs day-label" style="left:500px;">THU</div>
  <div class="abs day-label" style="left:636px;">FRI</div>
  <div class="abs day-label" style="left:758px;">SAT</div>

  <div class="abs notice">If you are unable to keep your appointment, kindly give 48 hours notice</div>
</section>

</body>
</html>
```